Senior sex novelty store providing a private method for acquiring the products and knowledge

Our business supplies novelty sex products and services, specializing in the 50+ demographic. Products include sex products for individuals and couples. Services include webinars and teleseminars that address various sex and relationship issues. We are dedicated to providing discreet delivery of products and knowledge to people over 50 entering a new phase of life, facing new challenges. Our entire process from site through shipping is kept private to allow our customers the freedom to shop and learn in the privacy of their own home.

Target Market(s)

Seniors over 50 years old

Industry/Entity Type

Store

Number of Pages Required

1 page

Font styles to use
Serif

Requirements
Must have
• place for business description with a private look
Should not have
• anything sleazy

```html
<!DOCTYPE html>
<html lang="en">
<head>
<meta charset="utf-8">
<title>Velvet Hour</title>
<link href="https://fonts.googleapis.com/css2?family=Playfair+Display:wght@400;600;700&display=swap" rel="stylesheet">
<style>
  :root {
    --bar-bg: #f4f4f4;
    --bar-text: #444444;
    --hero-dark: #121212;
    --hero-mid: #3a3230;
    --hero-warm: #6b5650;
    --accent: #e0141e;
    --white: #ffffff;
    --muted: #cfcfcf;
  }
  * { margin: 0; padding: 0; box-sizing: border-box; }
  html, body { width: 1200px; height: 800px; overflow: hidden; background: var(--hero-dark); }
  body { font-family: "Playfair Display", serif; position: relative; }

  .utility-bar {
    position: absolute; top: 0; left: 0; width: 1200px; height: 34px;
    background: var(--bar-bg);
    display: flex; align-items: center; justify-content: flex-end;
    padding-right: 80px; gap: 24px;
    font-size: 12px; color: var(--bar-text); z-index: 2;
  }
  .utility-bar .search { display: flex; align-items: center; gap: 6px; margin-left: 60px; }

  .hero-photo {
    position: absolute; top: 34px; left: 0; width: 1200px; height: 766px;
    background:
      radial-gradient(ellipse 300px 380px at 720px 330px, rgba(150,118,105,0.55), transparent 70%),
      radial-gradient(ellipse 260px 360px at 260px 280px, rgba(120,100,95,0.45), transparent 70%),
      linear-gradient(100deg, var(--hero-dark) 0%, var(--hero-mid) 35%, var(--hero-warm) 62%, var(--hero-mid) 82%, var(--hero-dark) 100%);
  }
  .hero-shade {
    position: absolute; top: 34px; left: 0; width: 1200px; height: 766px;
    background: linear-gradient(180deg, rgba(0,0,0,0.35) 0%, rgba(0,0,0,0.1) 40%, rgba(0,0,0,0.4) 100%);
  }

  .brand {
    position: absolute; top: 62px; left: 36px;
    display: flex; align-items: center; gap: 12px; z-index: 2;
  }
  .brand-square { width: 42px; height: 42px; background: var(--accent); }
  .brand-name { font-size: 18px; font-weight: 600; color: var(--white); letter-spacing: 1px; }

  .main-nav {
    position: absolute; top: 96px; left: 440px;
    display: flex; gap: 36px; z-index: 2;
    font-size: 12px; font-weight: 600; letter-spacing: 1.5px; color: var(--white);
  }
  .menu-toggle { position: absolute; top: 150px; right: 70px; z-index: 2; }

  .hero-copy {
    position: absolute; top: 420px; left: 140px; width: 800px;
    text-align: center; z-index: 2; color: var(--white);
  }
  .hero-ornament { display: block; margin: 0 auto 12px; }
  .hero-title {
    font-size: 40px; font-weight: 600; letter-spacing: 1px; text-transform: uppercase;
    white-space: nowrap;
  }
  .hero-title .highlight { color: var(--accent); }
  .hero-sub { margin-top: 14px; font-size: 13px; font-style: italic; color: var(--muted); letter-spacing: 1px; }
  .scroll-hint { position: absolute; top: 620px; left: 529px; z-index: 2; }
</style>
</head>
<body>
  <header class="utility-bar">
    <span>Shipping</span>
    <span>About company</span>
    <span>Contacts</span>
    <span class="search">
      <svg width="11" height="11" viewBox="0 0 12 12"><circle cx="5" cy="5" r="3.8" fill="none" stroke="#e0141e" stroke-width="1.5"/><line x1="8" y1="8" x2="11" y2="11" stroke="#e0141e" stroke-width="1.5"/></svg>
      Search
    </span>
  </header>

  <div class="hero-photo" role="img" aria-label="Photograph of an elegant couple in evening wear, the man holding a finger to his lips"></div>
  <div class="hero-shade"></div>

  <div class="brand">
    <span class="brand-square"></span>
    <span class="brand-name">Velvet Hour</span>
  </div>

  <nav class="main-nav">
    <span>HOME</span>
    <span>PRODUCTS</span>
    <span>BOOKS</span>
    <span>GIFTS</span>
  </nav>

  <svg class="menu-toggle" width="20" height="16" viewBox="0 0 20 16">
    <rect y="1" width="20" height="2" fill="#ffffff"/>
    <rect y="7" width="20" height="2" fill="#ffffff"/>
    <rect y="13" width="20" height="2" fill="#ffffff"/>
  </svg>

  <section class="hero-copy">
    <svg class="hero-ornament" width="140" height="16" viewBox="0 0 140 16">
      <line x1="0" y1="8" x2="58" y2="8" stroke="#ffffff" stroke-width="1"/>
      <line x1="82" y1="8" x2="140" y2="8" stroke="#ffffff" stroke-width="1"/>
      <path d="M70 14 L63 7 A3.5 3.5 0 0 1 70 3.5 A3.5 3.5 0 0 1 77 7 Z" fill="#e0141e"/>
    </svg>
    <h1 class="hero-title">Your <span class="highlight">Desires</span> Are Our <span class="highlight">Secret</span></h1>
    <p class="hero-sub">discreet care after fifty</p>
  </section>

  <svg class="scroll-hint" width="22" height="36" viewBox="0 0 22 36">
    <rect x="1" y="1" width="20" height="34" rx="10" fill="none" stroke="#ffffff" stroke-width="2"/>
    <line x1="11" y1="8" x2="11" y2="15" stroke="#ffffff" stroke-width="2"/>
  </svg>
</body>
</html>
```